Upmarket Dessert Lounge needs a Business Card Design

We are an upmarket dessert lounge needing a business card to match our image.

We want something that is simple yet beautiful, feminine, classy, sophisticated and elegant. We want it to stand out and don't mind if it is bold.

The design should include our logo and colours of red or maroon with gold highlights. We don't mind if black is used.

Marlow & Quince

Target Market(s)

For those who like to indulge or treat themselves and give in to their temptations on good quality desserts.

Industry/Entity Type

Business

Requirements
Must have
• Must include our logo and our name

Marlow & Quince

M & Q

```html
<!DOCTYPE html>
<html lang="en">
<head>
<meta charset="utf-8">
<title>Marlow &amp; Quince — Business Cards</title>
<link rel="stylesheet" href="https://fonts.googleapis.com/css2?family=Lora:wght@400;700&family=Open+Sans:wght@400;600&display=swap">
<style>
  :root {
    --maroon: #8e1a1c;
    --maroon-deep: #5e0d10;
    --maroon-light: #b0282a;
    --gold: #e6b27a;
    --peach: #f6c995;
    --paper: #ffffff;
    --ink: #ffffff;
    --backdrop: #d9d6d2;
    --title: #8a1c1e;
  }
  * { margin: 0; padding: 0; box-sizing: border-box; }
  html, body { width: 1200px; height: 951px; overflow: hidden; }
  body { background: var(--backdrop); position: relative; }

  .card {
    position: absolute;
    width: 620px;
    height: 354px;
    border-radius: 22px;
    overflow: hidden;
    box-shadow: 0 14px 30px rgba(0,0,0,0.25);
  }

  /* Front */
  .card--front {
    left: 70px; top: 80px;
    background: radial-gradient(ellipse at 45% 45%, var(--maroon-light) 0%, var(--maroon) 55%, var(--maroon-deep) 100%);
  }
  .card__ornament {
    position: absolute;
    right: 30px; top: 0;
    width: 250px; height: 100px;
    border-radius: 0 0 60px 60px;
    background: radial-gradient(ellipse at center, rgba(230,178,122,0.55) 0%, rgba(230,178,122,0.15) 60%, rgba(230,178,122,0) 100%);
  }
  .front__brand {
    position: absolute;
    left: 0; right: 0; top: 140px;
    text-align: center;
    font-family: "Lora", serif;
    font-weight: 400;
    font-size: 40px;
    letter-spacing: 2px;
    color: var(--gold);
  }
  .front__web {
    position: absolute;
    left: 0; right: 0; bottom: 42px;
    text-align: center;
    font-family: "Lora", serif;
    font-weight: 700;
    font-size: 17px;
    letter-spacing: 1px;
    color: var(--ink);
  }

  /* Back */
  .card--back {
    left: 510px; top: 500px;
    background: var(--paper);
  }
  .back__wave { position: absolute; inset: 0; }
  .back__brand {
    position: absolute;
    left: 40px; top: 58px;
    font-family: "Lora", serif;
    font-size: 24px;
    letter-spacing: 1px;
    color: var(--title);
  }
  .back__name {
    position: absolute;
    right: 34px; top: 40px;
    font-family: "Open Sans", sans-serif;
    font-weight: 400;
    font-size: 21px;
    color: var(--title);
  }
  .contact {
    position: absolute;
    right: 30px; bottom: 30px;
    list-style: none;
    font-family: "Open Sans", sans-serif;
    font-size: 16px;
    line-height: 24px;
    color: var(--ink);
    text-align: right;
  }
  .contact li { display: flex; align-items: center; justify-content: flex-end; gap: 8px; }
  .contact svg { width: 14px; height: 14px; flex: none; }
</style>
</head>
<body>

<section class="card card--front" aria-label="Business card front">
  <div class="card__ornament" role="img" aria-label="Gold floral flourish ornament"></div>
  <div class="front__brand">Marlow &amp; Quince</div>
  <div class="front__web">www.marlowquince.com</div>
</section>

<section class="card card--back" aria-label="Business card back">
  <svg class="back__wave" viewBox="0 0 620 354" preserveAspectRatio="none" aria-hidden="true">
    <defs>
      <radialGradient id="backMaroon" cx="50%" cy="70%" r="75%">
        <stop offset="0" stop-color="#b0282a"/>
        <stop offset="1" stop-color="#6a1013"/>
      </radialGradient>
    </defs>
    <path d="M0,200 C150,150 300,215 430,190 C520,172 580,150 620,138 L620,354 L0,354 Z" fill="#f6c995"/>
    <path d="M0,226 C160,182 300,240 430,215 C520,198 580,178 620,170 L620,354 L0,354 Z" fill="url(#backMaroon)"/>
  </svg>
  <div class="back__brand">Marlow &amp; Quince</div>
  <div class="back__name">Marlow &amp; Quince</div>
  <ul class="contact">
    <li>512-555-0140
      <svg viewBox="0 0 14 14" aria-hidden="true"><path d="M3 1 L5.5 1 L6.5 4 L5 5.3 C5.8 7 7 8.2 8.7 9 L10 7.5 L13 8.5 L13 11 C13 12 12 13 11 13 C5.5 13 1 8.5 1 3 C1 2 2 1 3 1 Z" fill="#f6c995"/></svg>
    </li>
    <li>512-555-0141
      <svg viewBox="0 0 14 14" aria-hidden="true"><rect x="4" y="1" width="6" height="4" fill="#f6c995"/><rect x="1" y="5" width="12" height="6" rx="1.5" fill="#f6c995"/><rect x="4" y="9" width="6" height="4" fill="#f6c995"/></svg>
    </li>
    <li>info@marlowquince.com
      <svg viewBox="0 0 14 14" aria-hidden="true"><rect x="1" y="3" width="12" height="8" rx="1" fill="#f6c995"/><path d="M1 3.5 L7 8 L13 3.5" fill="none" stroke="#8e1a1c" stroke-width="1"/></svg>
    </li>
    <li>www.marlowquince.com
      <svg viewBox="0 0 14 14" aria-hidden="true"><circle cx="7" cy="7" r="6" fill="#f6c995"/></svg>
    </li>
  </ul>
</section>

</body>
</html>
```